Foot and ankle surgeon requires a website design

I need a website where prospective and established patients can obtain information and then direct them to making appointments. My practice is a highly professional surgical practice specialising in surgery to the foot and ankle. My title is Mr Colin Brasket, Podiatric Foot & Ankle Surgeon. My qualifications are: BSc MSc FACPS
The practice website will require information on: Locations, phone numbers to make appointments, general background on podiatric surgery,
I would like to include information on: my hospital appointments, surgical fellowships held, training programs undertaken, association memberships, publications written, links to useful websites
A page dedicated to common foot conditions would be useful and also a page with referral information including an online registration section that will be sent direct to the receptionist.
Examples of similar websites include:
http://www.dorvelquintaro.com.au/
http://www.haldenfootsurgeon.com.au/
I will provide files on logo, self photos and my personal training history etc.
Also if there is going to be a background theme I personally am associated with surfing and beach activities, it would be great if this was able to be reflected in the design.
Thank you.

```html
<!DOCTYPE html>
<html lang="en">
<head>
<meta charset="utf-8">
<title>Mr Colin Brasket – Podiatric Foot &amp; Ankle Surgeon</title>
<link href="https://fonts.googleapis.com/css2?family=Ubuntu:wght@400;500&display=swap" rel="stylesheet">
<style>
  :root{
    --navy:#154f86;
    --navy-text:#1a4f84;
    --orange:#e8730c;
    --text:#4a4a4a;
    --muted:#5a5a5a;
    --panel:#ffffff;
    --line:#d6d6d6;
    --bg-a:#e9e6e3;
    --bg-b:#cfc6bf;
    --bg-c:#efe9e4;
  }
  *{box-sizing:border-box;margin:0;padding:0}
  html,body{width:1200px;height:1088px;overflow:hidden}
  body{font-family:"Ubuntu",sans-serif;color:var(--text);position:relative;
    background:linear-gradient(120deg,var(--bg-c) 0%,var(--bg-a) 30%,var(--bg-b) 60%,var(--bg-a) 85%,#d8cfc8 100%)}
  .box{position:absolute;background:var(--panel);border:1px solid var(--line)}
  .site-header{left:120px;top:29px;width:958px;height:108px}
  .brand{position:absolute;left:26px;top:36px;display:flex;align-items:center;gap:12px}
  .brand-dot{width:26px;height:26px;border-radius:50%;background:var(--navy)}
  .brand-name{font-size:28px;font-weight:500;color:var(--navy)}
  .header-phone{position:absolute;right:22px;top:38px;display:flex;align-items:center;gap:10px;font-size:26px;color:#555}
  .main-nav{left:120px;top:149px;width:958px;height:36px;display:flex;align-items:center;padding:0 8px}
  .main-nav a{font-size:15px;color:#444;text-decoration:none;padding:0 13px;border-left:1px solid #bbb;line-height:18px}
  .main-nav a:first-child{border-left:none;padding-left:0}
  .main-nav a:last-child{padding-right:0}
  .hero{position:absolute;left:120px;top:195px;width:958px;height:375px;
    background:linear-gradient(100deg,#3b2a24 0%,#7a5a4c 28%,#d8b3a0 50%,#eae4e0 66%,#4b5a78 85%,#e2ddd9 100%)}
  .hero-title{position:absolute;left:114px;top:128px;font-size:30px;line-height:38px;color:#fff;font-weight:400}
  .btn{display:inline-block;background:var(--orange);color:#fff;font-size:12px;text-transform:uppercase;
    border-radius:3px;box-shadow:0 2px 2px rgba(0,0,0,.25);text-align:center}
  .hero .btn{position:absolute;left:114px;top:217px;width:76px;height:26px;line-height:26px}
  .slide-arrow{position:absolute;top:358px;width:47px;height:50px;background:rgba(255,255,255,.9);border:1px solid #ccc;border-radius:3px;display:flex;align-items:center;justify-content:center}
  .slide-arrow.prev{left:94px}
  .slide-arrow.next{left:1056px}
  .intro{left:120px;top:583px;width:958px;height:205px}
  .surgeon-photo{position:absolute;left:21px;top:25px;width:155px;height:156px;background:linear-gradient(180deg,#7ea4b8 0%,#2f9a7d 55%,#2a8a6f 100%)}
  .about{position:absolute;left:216px;top:26px;width:360px}
  .about h2{font-size:20px;font-weight:400;color:var(--navy-text);margin-bottom:25px}
  .about p{font-size:11.5px;line-height:21px;color:var(--muted)}
  .appointment{position:absolute;left:623px;top:25px;width:310px;height:155px;background:var(--navy);color:#fff}
  .appointment svg{position:absolute;left:12px;top:21px}
  .appointment h3{position:absolute;left:115px;top:23px;font-size:17px;font-weight:400}
  .appointment p{position:absolute;left:115px;top:59px;font-size:12px;line-height:21px;width:180px}
  .appointment .btn{position:absolute;left:117px;top:109px;width:86px;height:28px;line-height:28px}
  .site-footer{left:120px;top:814px;width:958px;height:206px}
  .rule{position:absolute;left:6px;width:900px;height:1px;background:var(--line)}
  .footer-brand{position:absolute;left:53px;top:65px;display:flex;align-items:center;gap:8px}
  .footer-brand .brand-dot{width:18px;height:18px}
  .footer-brand .brand-name{font-size:17px}
  .legal{position:absolute;left:6px;top:128px;font-size:13px;line-height:22px;color:var(--muted)}
  .locations h2{position:absolute;left:380px;top:42px;font-size:19px;font-weight:400;color:var(--navy-text)}
  .location{position:absolute;top:82px}
  .location h4{font-size:13px;font-weight:400;color:var(--orange);margin-bottom:16px}
  .location address{font-style:normal;font-size:12.5px;line-height:17px;color:var(--muted)}
</style>
</head>
<body>
  <header class="box site-header">
    <div class="brand"><span class="brand-dot"></span><span class="brand-name">Mr Colin Brasket</span></div>
    <div class="header-phone">
      <svg width="26" height="20" viewBox="0 0 26 20"><path d="M2 7c0-4 22-4 22 0v3h-6V7.5H8V10H2z" fill="#e8730c"/><rect x="6" y="10" width="14" height="9" rx="2" fill="#e8730c"/><circle cx="13" cy="14.5" r="2.5" fill="#fff"/></svg>
      08 9721 5860
    </div>
  </header>

  <nav class="box main-nav">
    <a href="#">Home</a><a href="#">Appointments</a><a href="#">Surgical Fellowships</a><a href="#">Training Programs</a><a href="#">Memberships</a><a href="#">Publications</a><a href="#">Useful Websites</a><a href="#">Contact us</a>
  </nav>

  <section class="hero" role="img" aria-label="Photo of a gloved surgeon treating the sole of a patient's foot">
    <h1 class="hero-title">AUCTOR ALIQUETESR<br>NEANICITUDIN</h1>
    <a class="btn" href="#">More</a>
  </section>
  <a class="slide-arrow prev" href="#" aria-label="Previous slide"><svg width="16" height="22" viewBox="0 0 16 22"><path d="M13 2L4 11l9 9" fill="none" stroke="#e8730c" stroke-width="4"/></svg></a>
  <a class="slide-arrow next" href="#" aria-label="Next slide"><svg width="16" height="22" viewBox="0 0 16 22"><path d="M3 2l9 9-9 9" fill="none" stroke="#e8730c" stroke-width="4"/></svg></a>

  <section class="box intro">
    <div class="surgeon-photo" role="img" aria-label="Photo of a surgeon in green scrubs pulling on gloves in an operating theatre"></div>
    <div class="about">
      <h2>About Podiatric Foot &amp; Ankle Surgery</h2>
      <p>Morbi accumsan ipsum velit. Nam nec tellus a odio tincidunt auctor a ornare odio. Sed non mauris vitae erat consequat auctor eu in elit. Class aptent taciti sociosqu ad litora torquent per conubia nostra, per inceptos himenaeos.</p>
    </div>
    <div class="appointment">
      <svg width="70" height="76" viewBox="0 0 70 76"><circle cx="35" cy="35" r="31" fill="none" stroke="#fff" stroke-width="6"/><path d="M33 15v22l9 14" fill="none" stroke="#fff" stroke-width="4" stroke-linecap="round"/><ellipse cx="14" cy="68" rx="7" ry="6" fill="#fff"/><ellipse cx="56" cy="68" rx="7" ry="6" fill="#fff"/></svg>
      <h3>Make An Appointment</h3>
      <p>Schedule your appointment online.</p>
      <a class="btn" href="#">Click Here</a>
    </div>
  </section>

  <footer class="box site-footer">
    <div class="rule" style="top:10px"></div>
    <div class="footer-brand"><span class="brand-dot"></span><span class="brand-name">Mr Colin Brasket</span></div>
    <div class="legal">Copyright ©2014. All rights reserved.<br>Terms of Use | Terms of Sale | Privacy Policy | Disclaimer</div>
    <div class="locations">
      <h2>Our Locations</h2>
      <div class="location" style="left:380px"><h4>Port Alder</h4><address>42 Seabreeze Parade,<br>PO BOX 2841,<br>Port Alder WA 6532<br>Ph: 08 9721 5860<br>Fax: 08 9721 5875</address></div>
      <div class="location" style="left:617px"><h4>Bay End, Port Alder</h4><address>7C &amp; 7D Harlow Street,<br>Port Alder 6532.<br>Ph: 9721 6342<br>Fax: 9721 6350</address></div>
      <div class="location" style="left:802px"><h4>Redvale</h4><address>3/14 Quarry Lane,<br>Redvale WA 6435<br>Ph: 08 9054 2219<br>Fax: 08 9054 2230</address></div>
    </div>
    <div class="rule" style="top:195px"></div>
  </footer>
</body>
</html>
```